Web Design / Transformation our Joomla web site

Job Type
We are looking for a fresh eye-catching Custom Joomla Design to transform our Joomla web site

Task Description
We are in a process to create web site to Speech Pathology services . The site is built by using brightpanel ((http://www.brightpanel-demo.com/) meadow template.

You can see our site http://beyondtalkclinic-demo.com/demo

Unfortunately, this template does not match our identity. We would like to improve or replace it. Although we like features that brightpanel template is giving as part of their template ,we want to transform our site to something more simplistic and kids oriented . We don’t like look and fill of our website since it’s very professional and “corporate” . Our business is very small and is not 100 people company , we are looking for something more simple and personal. It should look professional, all be it, child friendly. We work on children’s communication skills, and we want to convey an idea that communication is “Beyond The Talk”, meaning children need to learn to play and socialize appropriately. In addition, learning to be a better communicators will help them to be closer to their family members and friends. We want our website to show kids playing and having fun. In other hand , we don't want the Website to be too busy with images, so use your professional judgment.
You can change current template or you can provide your own Joomla design.

Examples of website look that we like :

http://parentvoicehelp-demo.com
http://thevocalfriends-demo.blogspot.com/
http://brindleclinicvoice-demo.com/

About Our Company :
Company name: Beyond The Talk
What we do: Pediatric Speech & Language Pathology Services. We established Beyond The Talk to provide families with a unique option for their child’s speech therapy needs. Our clinic is founded on the principle that all children are different and require a thoughtful, parent-driven therapy plan. When a family chooses us, they will enter a partnership with an experienced, well-trained therapist.
Top Three Things to Communicate through our Website:
#1 - We are kids friendly
#2 - We are professional
#3 - We provide our services with a loving, nurturing attitude toward the child and with compassionate, comprehensive support and input for the family
Updates

To see current running site : http://beyondtalkclinic-demo.com/demo/

Reason: There are no good designs to address our needs

Reason: It's still work in progress. Submitted designs are still under constructions and waiting for updates

We are accepting WordPress designs as well !!!

Target Market(s)

Families with kids

Industry/Entity Type

Communication

Requirements
Must have
• • Joomla/Wordpress as a platform
• Easy to Navigate
• Clean Design, kids friendly but professional

```html
<!DOCTYPE html>
<html lang="en">
<head>
<meta charset="utf-8">
<title>Beyond The Talk — Speech &amp; Language Pathology Services</title>
<link rel="stylesheet" href="https://fonts.googleapis.com/css2?family=Open+Sans:wght@400;600&family=Noto+Serif:wght@400&display=swap">
<style>
:root{
  --sky-top:#5fb4e8;
  --sky-mid:#a9d8f4;
  --sky-pale:#e6f4fc;
  --nav-blue:#1ea4e3;
  --nav-blue-dark:#0b8ccc;
  --red:#d9252b;
  --blue-head:#1b9ad8;
  --green-head:#5a9e22;
  --green-deep:#2f6a1c;
  --grass:#8cbf45;
  --text:#8a8a8a;
  --title:#555;
  --white:#fff;
}
*{box-sizing:border-box;margin:0;padding:0}
html,body{width:710px;height:1200px;overflow:hidden;background:var(--white)}
body{position:relative;font-family:"Open Sans",Arial,sans-serif;color:var(--text)}
.abs{position:absolute}

/* header scenery */
.sky{left:0;top:0;width:710px;height:260px;background:linear-gradient(180deg,var(--sky-mid) 0%,var(--sky-top) 20%,var(--sky-mid) 55%,var(--sky-pale) 100%)}
.landscape{left:0;top:240px;width:710px;height:160px;background:linear-gradient(180deg,var(--sky-pale) 0%,#b9d98a 30%,var(--grass) 55%,#d6ebbd 80%,var(--white) 100%)}

.brand{left:58px;top:22px;width:120px}
.brand-mark{display:flex;align-items:center;gap:6px}
.brand-dot{width:14px;height:14px;border-radius:50%;background:var(--red);flex:none}
.brand-name{font-family:"Noto Serif",Georgia,serif;font-size:20px;line-height:22px;color:var(--red);width:100px}
.brand-tag{font-size:5.4px;color:var(--nav-blue-dark);font-weight:600;margin-top:4px;white-space:nowrap}

.search{left:491px;top:75px;width:164px;height:20px;background:var(--white);border:1px solid #cfe3ef;border-radius:2px;font-size:6.5px;font-style:italic;color:#999;padding:5px 8px}
.search svg{position:absolute;right:6px;top:4px}

.nav{left:55px;top:105px;width:599px;height:29px;background:linear-gradient(180deg,#35b4ef,var(--nav-blue-dark));display:flex}
.nav a{color:var(--white);text-decoration:none;font-size:9.6px;line-height:29px;padding:0 15px;border-right:1px solid rgba(255,255,255,.35)}
.nav a:last-child{border-right:none}

/* hero */
.hero{left:55px;top:134px;width:599px;height:226px}
.hero-title{left:96px;top:178px;font-family:"Noto Serif",Georgia,serif;font-weight:400;font-size:20.5px;line-height:25px;color:var(--red)}
.hero-text{left:97px;top:230px;width:220px;font-size:6.9px;line-height:11.4px;color:var(--blue-head)}
.btn-more{left:97px;top:271px;width:61px;height:19px;background:linear-gradient(180deg,#82c93a,#4f9a1c);border-radius:2px;color:var(--white);font-size:6.5px;font-weight:600;text-align:center;line-height:19px}
.hero-arrows{left:98px;top:300px}
.hero-photo{left:364px;top:148px;width:276px;height:182px}

/* main posts */
.post{left:59px;width:382px}
.post h2{font-family:"Noto Serif",Georgia,serif;font-weight:400;font-size:14px;line-height:18px;color:var(--title);margin-bottom:5px}
.post p{font-size:7.1px;line-height:12.8px;color:var(--text);margin-bottom:6px}
.post .meta{font-size:7.4px;color:var(--red)}
.post .meta span{margin:0 4px}
.divider{left:59px;width:380px;border-top:1px dotted #999}

/* sidebar */
.sidebar{left:467px;top:388px;width:162px;height:641px;border-left:1px solid #e6e6e6}
.widget{position:absolute;left:16px;width:146px}
.widget h3{font-family:"Noto Serif",Georgia,serif;font-weight:400;font-size:13.5px;line-height:18px;margin-bottom:5px}
.widget ul{list-style:none}
.widget li{font-size:7.1px;line-height:17.6px;padding-left:13px;position:relative}
.widget li::before{content:"";position:absolute;left:2px;top:6px;border-left:4px solid #999;border-top:2.5px solid transparent;border-bottom:2.5px solid transparent}
.cat h3{color:var(--red)}
.cat li{color:#666}
.pop h3{color:var(--blue-head)}
.pop .item{font-size:7.1px;line-height:11.6px;color:var(--text);padding:6px 0;border-bottom:1px solid #e6e6e6}
.pop .item:last-child{border-bottom:none}
.arch h3{color:var(--green-head)}
.arch li{color:var(--green-head)}
.sep{position:absolute;left:0;width:162px;border-top:1px solid #e3e3e3}

/* footer */
.flowers{left:0;top:1036px;width:710px;height:90px;background:linear-gradient(180deg,var(--white) 0%,#f7e07a 22%,#e9a818 50%,#7a5a14 78%,var(--green-deep) 100%)}
.footer{left:0;top:1118px;width:710px;height:82px;background:linear-gradient(180deg,#3d7e22,var(--green-deep))}
.foot-nav{left:58px;top:1145px;font-size:8px;color:var(--white);white-space:nowrap}
.foot-nav span{margin:0 5px}
.copyright{left:58px;top:1163px;font-size:6px;color:#b8d4a8}
.social{left:566px;top:1147px;display:flex;gap:5px}
.social i{display:block;width:18px;height:18px;border-radius:50%;background:var(--white)}
</style>
</head>
<body>

<div class="abs sky"></div>
<div class="abs landscape" role="img" aria-label="Illustrated countryside of green hills and fields behind the header"></div>

<svg class="abs hero" width="599" height="226" viewBox="0 0 599 226" aria-hidden="true">
  <defs>
    <linearGradient id="heroFill" x1="0" y1="0" x2="0" y2="1">
      <stop offset="0" stop-color="#f4f9fd"/>
      <stop offset="1" stop-color="#e3f0fa"/>
    </linearGradient>
  </defs>
  <path d="M0 0 H599 V214 Q470 186 330 200 T0 216Z" fill="url(#heroFill)"/>
</svg>

<header>
  <div class="abs brand">
    <div class="brand-mark"><span class="brand-dot"></span><span class="brand-name">Beyond The Talk</span></div>
    <div class="brand-tag">Speech &amp; Language Pathology Services</div>
  </div>

  <div class="abs search">Search here
    <svg width="11" height="11" viewBox="0 0 11 11"><circle cx="4.5" cy="4.5" r="3.5" fill="none" stroke="#999" stroke-width="1.2"/><line x1="7" y1="7" x2="10" y2="10" stroke="#999" stroke-width="1.4"/></svg>
  </div>

  <nav class="abs nav">
    <a>HOME</a><a>ABOUT US</a><a>TREATMENT TECHNIQUES</a><a>RECENT BLOG</a><a>FAQ</a><a>RESOURCES</a><a>CONTACT</a>
  </nav>
</header>

<section>
  <h1 class="abs hero-title">Duis sed tellus et<br>Phasellus felis dolor</h1>
  <p class="abs hero-text">Mauris vel lacus vitae felis vestibulum volutpat. Etiam est nunc, venenatis in, tristique eu, imperdiet ac, nisl. Cum sociis natoque penatibus et magnis dis parturient montes</p>
  <div class="abs btn-more">LEARN MORE</div>
  <svg class="abs hero-arrows" width="20" height="13" viewBox="0 0 20 13" aria-hidden="true">
    <polyline points="6,1 1,6.5 6,12" fill="none" stroke="var(--blue-head)" stroke-width="1.5"/>
    <polyline points="13,1 18,6.5 13,12" fill="none" stroke="var(--blue-head)" stroke-width="1.5"/>
  </svg>
  <svg class="abs hero-photo" width="276" height="182" viewBox="0 0 276 182" role="img" aria-label="Photo of a teacher reading to a group of young children in a classroom">
    <defs>
      <linearGradient id="photoTone" x1="0" y1="0" x2="1" y2="1">
        <stop offset="0" stop-color="#d9cdb4"/>
        <stop offset=".5" stop-color="#b7a58a"/>
        <stop offset="1" stop-color="#c9785a"/>
      </linearGradient>
    </defs>
    <path d="M0 0 H276 V182 Q200 168 138 176 T0 176Z" fill="var(--white)"/>
    <path d="M5 5 H271 V174 Q200 160 138 168 T5 168Z" fill="url(#photoTone)"/>
  </svg>
</section>

<main>
  <article class="abs post" style="top:393px">
    <h2>Nunc tempus felis vitae urna</h2>
    <p>Vivamus porttitor, g, purus nisi eleifend libero, a tempus libero lectus feugiat felis. Morbi diam mauris, viverra in, gravida eu, mattis in, ante. Morbi eget arcu. Morbi porta, libero id ullamcorper nonummy.</p>
    <p>Nibh ligula pulvinar metus, eget consectetuer augue nisi quis lacus. Ut ac mi quis lacus mollis aliquam. Curabitur iaculis tempus eros. Curabitur vel mi sit amet magna malesuada ultrices. Ut nisi erat, fermentum vel, congue id, euismod in, elit. Fusce ultricies, orci ac feugiat suscipit, leo massa sodales velit</p>
    <div class="meta">Learn More<span>|</span>2 Comments<span>|</span>Posted on June 15, 2013</div>
  </article>
  <div class="abs divider" style="top:520px"></div>

  <article class="abs post" style="top:534px">
    <h2>Phasellus felis dolor scelerisque tempus</h2>
    <p>Vivamus porttitor, g, purus nisi eleifend libero, a tempus libero lectus feugiat felis. Morbi diam mauris, viverra in, gravida eu, mattis in, ante. Morbi eget arcu. Morbi porta, libero id ullamcorper nonummy.</p>
    <p>Nibh ligula pulvinar metus, eget consectetuer augue nisi quis lacus. Ut ac mi quis lacus mollis aliquam. Curabitur iaculis tempus eros. Curabitur vel mi sit amet magna malesuada ultrices. Ut nisi erat, fermentum vel, congue id, euismod in, elit. Fusce ultricies, orci ac feugiat suscipit, leo massa sodales velit</p>
    <div class="meta">Learn More<span>|</span>2 Comments<span>|</span>Posted on June 15, 2013</div>
  </article>
  <div class="abs divider" style="top:665px"></div>

  <article class="abs post" style="top:682px">
    <h2>Duis sed tellus et tortor vestibulum gravida</h2>
    <p>Vivamus porttitor, g, purus nisi eleifend libero, a tempus libero lectus feugiat felis. Morbi diam mauris, viverra in, gravida eu, mattis in, ante. Morbi eget arcu. Morbi porta, libero id ullamcorper nonummy.</p>
    <p>Nibh ligula pulvinar metus, eget consectetuer augue nisi quis lacus. Ut ac mi quis lacus mollis aliquam</p>
    <div class="meta">Learn More<span>|</span>2 Comments<span>|</span>Posted on June 15, 2013</div>
  </article>
  <div class="abs divider" style="top:789px"></div>

  <article class="abs post" style="top:806px">
    <h2>Duis sed tellus et tortor vestibulum gravida</h2>
    <p>Vivamus porttitor, g, purus nisi eleifend libero, a tempus libero lectus feugiat felis. Morbi diam mauris, viverra in, gravida eu, mattis in, ante. Morbi eget arcu. Morbi porta, libero id ullamcorper nonummy.</p>
    <p>Nibh ligula pulvinar metus, eget consectetuer augue nisi quis lacus. Ut ac mi quis lacus mollis aliquam</p>
    <div class="meta">Learn More<span>|</span>2 Comments<span>|</span>Posted on June 15, 2013</div>
  </article>
  <div class="abs divider" style="top:913px"></div>

  <article class="abs post" style="top:928px">
    <h2>Curabitur vel mi sit amet magna malesuada</h2>
    <p>Vivamus porttitor, g, purus nisi eleifend libero, a tempus libero lectus feugiat felis. Morbi diam mauris, viverra in, gravida eu, mattis in, ante. Morbi eget arcu. Morbi porta, libero id ullamcorper nonummy.</p>
    <p>Nibh ligula pulvinar metus, eget consectetuer augue nisi quis lacus. Ut ac mi quis lacus mollis aliquam</p>
    <div class="meta">Learn More<span>|</span>2 Comments<span>|</span>Posted on June 15, 2013</div>
  </article>
</main>

<aside class="abs sidebar">
  <div class="widget cat" style="top:0">
    <h3>Our Category</h3>
    <ul>
      <li>Duis tincidunt lectus</li>
      <li>Wuis dui viverra vestibulum.</li>
      <li>Suspendisse vulputate aliquam dui.</li>
      <li>Nulla elementum dui</li>
      <li>Aliquam vehicula</li>
      <li>Maecenas placerat</li>
      <li>Nisl at consequat</li>
      <li>Sem nunc gravida</li>
      <li>Justo quis eleifend arcu</li>
    </ul>
  </div>
  <div class="sep" style="top:191px"></div>

  <div class="widget pop" style="top:202px">
    <h3>Popular Posts</h3>
    <div class="item">Donec scelerisque leo ac risus. Praesent sit amet est in dictum dolor eu dictum</div>
    <div class="item">Porttitor, enim felis viverra mi eget luctus</div>
    <div class="item">Etiam nulla massa pharetra facilisis, volut-pat in imperdiet sit amet sem</div>
    <div class="item">Aliquam nec erat at purus cursus interdum Vestibulum ligula</div>
  </div>
  <div class="sep" style="top:360px"></div>

  <div class="widget arch" style="top:373px">
    <h3>Blog Archive</h3>
    <ul>
      <li>July 2012</li>
      <li>February 2012</li>
      <li>January 2012</li>
      <li>December 2011</li>
      <li>November 2011</li>
      <li>October 2011</li>
      <li>September 2011</li>
      <li>August 2011</li>
      <li>July 2011</li>
    </ul>
  </div>
</aside>

<footer>
  <div class="abs flowers" role="img" aria-label="Illustrated field of sunflowers along the bottom of the page"></div>
  <div class="abs footer"></div>
  <div class="abs foot-nav">HOME<span>|</span>ABOUT US<span>|</span>TREATMENT TECHNIQUES<span>|</span>RECENT BLOG<span>|</span>FAQ<span>|</span>RESOURCES<span>|</span>CONTACT</div>
  <div class="abs copyright">Copyright © 2013 Company name. All right reserved</div>
  <div class="abs social" aria-label="Social media links"><i></i><i></i><i></i><i></i></div>
</footer>

</body>
</html>
```